Classy, Elegant, Simple Business Card Design

Looking to have a classy, simple, and elegant design. Want a top notch designed business card. I really like the look of the new torvane credit card. I also like the design I attached. I am trying to reach 21-29 year old females for booking us for there wedding or event. We offer Disc Jockey Service, Photo Booth Rentals, and Uplighting .

Target Market(s)

21-28 year old females

Contact Information for Business Card

Has to have logo, website, email, and phone number

Font styles to use
Other font styles liked:
• open to font choice, modern, clean
Designer to choose
33a6d7
0791cd
0555a3
ffffff

Requirements
Must have
• Has to have logo, website, email, and phone number
Nice to have
• I really like the design of the new torvane credit card. I also included my logo and some designs I like
Should not have
• clutter or too much info

```html
<!DOCTYPE html>
<html lang="en">
<head>
<meta charset="utf-8">
<title>Tidelight Event Group — Business Card</title>
<link rel="stylesheet" href="https://fonts.googleapis.com/css2?family=Jost:wght@400;500;600&display=swap">
<style>
  :root {
    --bg: #3a3a3c;
    --card: #1e1f22;
    --sky: #33a6d7;
    --blue: #0791cd;
    --deep: #0555a3;
    --white: #ffffff;
    --muted: #8a8d92;
  }
  * { box-sizing: border-box; margin: 0; padding: 0; }
  html, body { width: 799px; height: 1200px; overflow: hidden; }
  body {
    background: var(--bg);
    font-family: "Jost", sans-serif;
    position: relative;
  }
  .card {
    position: absolute;
    left: 80px;
    width: 640px;
    height: 366px;
    background: var(--card);
    border-radius: 4px;
    box-shadow: 0 14px 30px rgba(0,0,0,.45);
    overflow: hidden;
  }
  .card--front { top: 150px; }
  .card--back { top: 690px; }

  .brand { text-align: center; }
  .brand__name {
    font-weight: 500;
    font-size: 40px;
    letter-spacing: 3px;
    color: var(--blue);
    line-height: 1;
  }
  .brand__tag {
    margin-top: 8px;
    font-size: 15px;
    letter-spacing: 7px;
    color: var(--muted);
  }
  .card--front .brand {
    position: absolute;
    top: 110px; left: 0; right: 0;
  }
  .brand__dot {
    display: inline-block;
    width: 12px; height: 12px;
    border-radius: 50%;
    background: var(--sky);
    margin-bottom: 18px;
  }

  .equalizer {
    position: absolute;
    left: 0; right: 0; bottom: 0;
    height: 70px;
    background: linear-gradient(90deg, var(--sky), var(--blue) 55%, var(--deep));
    -webkit-mask: linear-gradient(180deg, rgba(0,0,0,.15), #000 70%);
            mask: linear-gradient(180deg, rgba(0,0,0,.15), #000 70%);
  }

  .card--back .brand {
    position: absolute;
    left: 30px; width: 260px; top: 130px;
  }
  .card--back .brand__name { font-size: 32px; letter-spacing: 2px; }
  .card--back .brand__tag { font-size: 12px; letter-spacing: 6px; }

  .divider {
    position: absolute;
    left: 320px; top: 90px;
    width: 2px; height: 190px;
    background: var(--muted);
    opacity: .7;
  }

  .contact {
    position: absolute;
    left: 360px; top: 120px;
    color: var(--white);
  }
  .contact__name {
    font-size: 26px;
    font-weight: 600;
    color: var(--blue);
    line-height: 1.1;
  }
  .contact__role {
    font-size: 15px;
    margin-bottom: 16px;
  }
  .contact__row {
    display: flex;
    align-items: center;
    gap: 12px;
    font-size: 16px;
    line-height: 26px;
  }
  .contact__row svg { width: 14px; height: 14px; fill: none; stroke: var(--blue); stroke-width: 2; }
</style>
</head>
<body>

  <section class="card card--front">
    <div class="brand">
      <span class="brand__dot"></span>
      <div class="brand__name">TIDELIGHT</div>
      <div class="brand__tag">EVENT GROUP</div>
    </div>
    <div class="equalizer" role="img" aria-label="Blue sound-wave equalizer bars along the bottom edge"></div>
  </section>

  <section class="card card--back">
    <div class="brand">
      <span class="brand__dot"></span>
      <div class="brand__name">TIDELIGHT</div>
      <div class="brand__tag">EVENT GROUP</div>
    </div>

    <div class="divider"></div>

    <div class="contact">
      <div class="contact__name">Mara Ellison</div>
      <div class="contact__role">Founder &amp; CEO</div>
      <div class="contact__row">
        <svg viewBox="0 0 16 16"><path d="M3 2h3l1 3-2 1a8 8 0 0 0 5 5l1-2 3 1v3c0 1-1 1-1 1C7 14 2 9 2 3c0 0 0-1 1-1z"/></svg>
        <span>555 0142 0188</span>
      </div>
      <div class="contact__row">
        <svg viewBox="0 0 16 16"><rect x="1.5" y="3.5" width="13" height="9"/><path d="M1.5 3.5 8 9l6.5-5.5"/></svg>
        <span>mara@tidelight.com</span>
      </div>
      <div class="contact__row">
        <svg viewBox="0 0 16 16"><circle cx="8" cy="8" r="6.5"/><path d="M1.5 8h13M8 1.5c-3 3.5-3 9.5 0 13M8 1.5c3 3.5 3 9.5 0 13"/></svg>
        <span>www.tidelight.com</span>
      </div>
    </div>
  </section>

</body>
</html>
```